TALMORK

The business want a professional looking business card. We have a scetch we will add but want the extra upgrade, and would like more suggestions for variations of our business cards.

```html
<!DOCTYPE html>
<html lang="en">
<head>
<meta charset="utf-8">
<title>TALMORK business card</title>
<link rel="stylesheet" href="https://fonts.googleapis.com/css2?family=Playfair+Display:wght@500;700&family=Poppins:wght@400&display=swap">
<style>
  :root {
    --page: #e9e7e3;
    --card: #232323;
    --gold: #c9a546;
    --ink: #f2f2f2;
    --emboss: #2d2d2d;
    --emboss-dot: #141414;
  }
  * { margin: 0; padding: 0; box-sizing: border-box; }
  html, body { width: 1200px; height: 900px; overflow: hidden; background: var(--page); }
  .canvas {
    width: 1200px; height: 900px;
    display: flex; flex-direction: column; align-items: center; justify-content: center; gap: 40px;
  }
  .card {
    width: 700px; height: 400px; border-radius: 22px;
    background: var(--card);
    box-shadow: 0 12px 30px rgba(0,0,0,.25);
    position: relative; overflow: hidden;
  }
  /* front */
  .card-front { display: flex; flex-direction: column; align-items: center; justify-content: center; gap: 26px; }
  .brand-dot { width: 38px; height: 38px; border-radius: 50%; background: var(--gold); }
  .wordmark {
    font-family: "Playfair Display", serif; font-weight: 500; color: var(--gold);
    letter-spacing: .32em; padding-left: .32em;
  }
  .card-front .wordmark { font-size: 62px; }
  /* back */
  .card-back { padding: 56px 0 0 58px; }
  .back-brand { display: flex; flex-direction: column; align-items: flex-start; gap: 14px; }
  .back-brand .brand-dot { width: 20px; height: 20px; margin-left: 92px; }
  .back-brand .wordmark { font-size: 32px; }
  .holder-name {
    margin-top: 34px;
    font-family: "Playfair Display", serif; font-weight: 700; font-size: 26px; color: var(--gold);
  }
  .holder-role, .holder-person {
    font-family: "Poppins", sans-serif; font-size: 16px; color: var(--ink); line-height: 1.35;
  }
  .contact-list { list-style: none; margin-top: 34px; display: flex; flex-direction: column; gap: 8px; }
  .contact-list li {
    display: flex; align-items: center; gap: 10px;
    font-family: "Poppins", sans-serif; font-size: 16px; color: var(--ink);
  }
  .contact-list svg { width: 14px; height: 14px; fill: var(--gold); flex: none; }
  .emboss-mark {
    position: absolute; right: 46px; top: 150px;
    display: flex; align-items: center; gap: 18px;
  }
  .emboss-mark .brand-dot { width: 46px; height: 46px; background: var(--emboss-dot); }
  .emboss-mark .wordmark { font-size: 44px; color: var(--emboss); letter-spacing: .12em; padding-left: 0; }
</style>
</head>
<body>
<main class="canvas">
  <section class="card card-front" aria-label="Card front">
    <span class="brand-dot" aria-hidden="true"></span>
    <h1 class="wordmark">TALMORK</h1>
  </section>

  <section class="card card-back" aria-label="Card back">
    <div class="back-brand">
      <span class="brand-dot" aria-hidden="true"></span>
      <p class="wordmark">TALMORK</p>
    </div>
    <h2 class="holder-name">Talmork Vestheim</h2>
    <p class="holder-role">CEO &amp; Founder</p>
    <p class="holder-person">Arne Olav Brekkestad</p>
    <ul class="contact-list">
      <li><svg viewBox="0 0 16 16"><path d="M3 1h3l1.5 4-2 1.2a9 9 0 0 0 4.3 4.3L11 8.5l4 1.5v3a2 2 0 0 1-2 2A12 12 0 0 1 1 3a2 2 0 0 1 2-2z"/></svg>004795551027</li>
      <li><svg viewBox="0 0 16 16"><path d="M1 3h14v10H1z M1 3l7 6 7-6" fill="none" stroke="#c9a546" stroke-width="1.8"/></svg>talmork.llc@mailbox.com</li>
      <li><svg viewBox="0 0 16 16"><circle cx="8" cy="8" r="6.5" fill="none" stroke="#c9a546" stroke-width="1.6"/><path d="M1.5 8h13M8 1.5c3 3.5 3 9.5 0 13M8 1.5c-3 3.5-3 9.5 0 13" fill="none" stroke="#c9a546" stroke-width="1.2"/></svg>www.talmork.llc</li>
    </ul>
    <div class="emboss-mark" aria-hidden="true">
      <span class="brand-dot"></span>
      <span class="wordmark">TALMORK</span>
    </div>
  </section>
</main>
</body>
</html>
```